Marlow Estate Fixers (Handyman / Home Improvement Company)

Looking for a double sided professional looking business card with Logo attached to be highlighted on one side and throwing in an image of a handyman as an option would be nice to see as well. We are a company focused on providing quality Handyman and Home improvement services in a timely manner that is done right the first time with integrity

Industry/Entity Type

Handyman / Home Improvement

Contact Information for Business Card

(LOGO, Name, Mobile and office phone numbers, email) on front side of card, (the words "The SOLUTION to all of your Handyman and Home Improvement needs" followed by "Family Owned and Operated" at the very bottom) on the back.

Colors
EB3D1F
EC4F4E
F09395
F8D3D4
FCEDEE

Requirements
Must have
• Red, Gray, Black Color scheme
Should not have
• No Yellow or Blue colors

```html
<!DOCTYPE html>
<html lang="en">
<head>
<meta charset="utf-8">
<title>Marlow Estate Fixers – Business Card</title>
<link rel="stylesheet" href="https://fonts.googleapis.com/css2?family=Lato:ital,wght@0,400;0,700;0,900;1,400&display=swap">
<style>
  :root {
    --red: #e5202a;
    --ink: #1c1c1d;
    --card-dark: #1e1e1f;
    --paper: #ffffff;
    --stage: #3a3d40;
    --grey-text: #2b2b2c;
    --light: #f2f2f2;
    --rule: #8a8a8a;
  }
  * { box-sizing: border-box; margin: 0; padding: 0; }
  html, body {
    width: 1200px; height: 1122px; overflow: hidden;
    background: var(--stage);
    font-family: "Lato", sans-serif;
  }
  .card {
    position: absolute; left: 170px;
    width: 860px; height: 492px;
    border-radius: 26px;
  }
  .card--front { top: 52px; background: var(--paper); }
  .card--back { top: 578px; background: var(--card-dark); }

  /* wordmark stand-in */
  .brand {
    display: flex; align-items: center; gap: 16px;
  }
  .brand__dot {
    width: 34px; height: 34px; border-radius: 50%;
    background: var(--red); flex: none;
  }
  .brand__name {
    font-weight: 900; text-transform: uppercase;
    letter-spacing: 1px; line-height: 1.05;
  }

  .card--front .brand {
    position: absolute; left: 0; right: 0; top: 110px;
    justify-content: center;
  }
  .card--front .brand__name { color: var(--ink); font-size: 46px; }

  .tagline {
    position: absolute; left: 0; right: 0; top: 300px;
    text-align: center; color: var(--grey-text);
  }
  .tagline__line {
    font-weight: 900; font-size: 25px; letter-spacing: 1px;
    text-transform: uppercase; line-height: 1.3;
  }
  .tagline__accent { color: var(--red); }
  .tagline__sub {
    margin-top: 6px; color: var(--red);
    font-style: italic; font-size: 19px;
  }

  .card--back .brand {
    position: absolute; left: 60px; top: 210px; width: 330px;
    gap: 14px;
  }
  .card--back .brand__name { color: var(--light); font-size: 30px; }
  .card--back .brand__dot { width: 26px; height: 26px; }

  .divider {
    position: absolute; left: 420px; top: 110px;
    width: 1px; height: 272px; background: var(--rule);
  }
  .contact {
    position: absolute; left: 470px; top: 118px; color: var(--light);
  }
  .contact__name {
    font-weight: 900; font-size: 36px; letter-spacing: 1px;
    text-transform: uppercase;
  }
  .contact__role { color: var(--red); font-size: 20px; margin-top: 2px; }
  .contact__list { list-style: none; margin-top: 22px; }
  .contact__item {
    display: flex; align-items: center; gap: 16px;
    font-size: 19px; letter-spacing: .5px; height: 36px;
  }
  .contact__icon { width: 18px; height: 18px; flex: none; fill: var(--red); }
</style>
</head>
<body>

<section class="card card--front" aria-label="Card front">
  <div class="brand">
    <span class="brand__dot"></span>
    <span class="brand__name">Marlow Estate Fixers</span>
  </div>
  <div class="tagline">
    <p class="tagline__line">Your <span class="tagline__accent">Solution</span> to all of your</p>
    <p class="tagline__line">Handyman &amp; Home Improvement Needs</p>
    <p class="tagline__sub">Family Owned &amp; Operated</p>
  </div>
</section>

<section class="card card--back" aria-label="Card back">
  <div class="brand">
    <span class="brand__dot"></span>
    <span class="brand__name">Marlow Estate Fixers</span>
  </div>
  <div class="divider"></div>
  <div class="contact">
    <h1 class="contact__name">Daniel Reyes</h1>
    <p class="contact__role">Founder &amp; CEO</p>
    <ul class="contact__list">
      <li class="contact__item">
        <svg class="contact__icon" viewBox="0 0 24 24" aria-hidden="true"><path d="M6.6 10.8a15.2 15.2 0 0 0 6.6 6.6l2.2-2.2a1 1 0 0 1 1-.25 11.4 11.4 0 0 0 3.6.57 1 1 0 0 1 1 1V20a1 1 0 0 1-1 1A17 17 0 0 1 3 4a1 1 0 0 1 1-1h3.5a1 1 0 0 1 1 1c0 1.25.2 2.45.57 3.6a1 1 0 0 1-.25 1z"/></svg>
        (123) 456-7890
      </li>
      <li class="contact__item">
        <svg class="contact__icon" viewBox="0 0 24 24" aria-hidden="true"><path d="M7 1h10a2 2 0 0 1 2 2v18a2 2 0 0 1-2 2H7a2 2 0 0 1-2-2V3a2 2 0 0 1 2-2zm0 3v14h10V4zm5 15.5a1 1 0 1 0 0 2 1 1 0 0 0 0-2z"/></svg>
        (123) 456-7890
      </li>
      <li class="contact__item">
        <svg class="contact__icon" viewBox="0 0 24 24" aria-hidden="true"><path d="M2 5h20v14H2zm2 2v.5l8 5 8-5V7l-8 5z"/></svg>
        info@marlowfixers.com
      </li>
      <li class="contact__item">
        <svg class="contact__icon" viewBox="0 0 24 24" aria-hidden="true"><path d="M12 2a10 10 0 1 0 0 20 10 10 0 0 0 0-20zm6.9 6h-2.9a15.6 15.6 0 0 0-1.4-3.6A8 8 0 0 1 18.9 8zM12 4c.8 1.2 1.5 2.5 1.9 4h-3.8c.4-1.5 1.1-2.8 1.9-4zM4.3 14a8.2 8.2 0 0 1 0-4h3.4a16.5 16.5 0 0 0 0 4zm.8 2h2.9c.3 1.3.8 2.5 1.4 3.6A8 8 0 0 1 5.1 16zM8 8H5.1a8 8 0 0 1 4.3-3.6C8.8 5.5 8.4 6.7 8 8zm4 12c-.8-1.2-1.5-2.5-1.9-4h3.8c-.4 1.5-1.1 2.8-1.9 4zm2.3-6H9.7a14.7 14.7 0 0 1 0-4h4.6a14.7 14.7 0 0 1 0 4zm.3 5.6c.6-1.1 1.1-2.3 1.4-3.6h2.9a8 8 0 0 1-4.3 3.6zm1.7-5.6a16.5 16.5 0 0 0 0-4h3.4a8.2 8.2 0 0 1 0 4z"/></svg>
        marlowfixers.com
      </li>
    </ul>
  </div>
</section>

</body>
</html>
```